Business card design for my company.
I would like the card's background colour to be black. You can also see our web site to get an idea of our brand. https://www.tmwhomecrafting.com.au/
- Name
- Email

```html
<!DOCTYPE html>
<html lang="en">
<head>
<meta charset="UTF-8">
<title>TMW Home Crafting – Business Card</title>
<link rel="stylesheet" href="https://fonts.googleapis.com/css2?family=Poppins:wght@400;500;600;700&display=swap">
<style>
  :root {
    --stage: #1a1a1d;
    --card: #222524;
    --white: #ffffff;
    --silver: #a9abad;
    --green: #1f9a46;
    --text: #f2f2f2;
  }
  * { box-sizing: border-box; margin: 0; padding: 0; }
  html, body {
    width: 1200px; height: 800px; overflow: hidden;
    background: var(--stage);
    font-family: "Poppins", sans-serif;
  }
  .stage {
    width: 1200px; height: 800px;
    display: flex; flex-direction: column; align-items: center;
    justify-content: center; gap: 34px;
  }
  .card {
    width: 600px; height: 343px;
    background: var(--card);
    border-radius: 22px;
    position: relative;
    overflow: hidden;
    box-shadow: 0 14px 30px rgba(0,0,0,.45);
  }
  .brand {
    display: flex; align-items: center; gap: 12px;
    font-weight: 700; letter-spacing: 2px; text-transform: uppercase;
  }
  .brand-mark { width: 16px; height: 16px; flex: none; }
  .card-front .brand {
    position: absolute; inset: 0; justify-content: center;
    font-size: 30px; color: var(--silver);
  }
  .card-front .brand-mark { background: var(--silver); }
  .card-back .brand {
    position: absolute; left: 44px; top: 50%;
    transform: translateY(-50%);
    width: 230px;
    font-size: 24px; line-height: 1.15; color: var(--white);
  }
  .card-back .brand-mark { background: var(--green); }
  .brand-line { display: block; white-space: nowrap; }
  .divider {
    position: absolute; left: 300px; top: 70px;
    width: 1.5px; height: 200px; background: var(--green);
  }
  .contact {
    position: absolute; left: 326px; top: 78px; right: 20px; color: var(--text);
  }
  .contact-name {
    color: var(--green); font-weight: 700; font-size: 21px;
    text-transform: uppercase; letter-spacing: .5px; line-height: 1.1;
  }
  .contact-role {
    font-size: 12px; text-transform: uppercase; letter-spacing: .5px;
    margin-bottom: 22px;
  }
  .contact-list { list-style: none; }
  .contact-list li {
    display: flex; align-items: center; gap: 9px;
    font-size: 11.5px; margin-bottom: 9px; white-space: nowrap;
  }
  .contact-icon { width: 18px; height: 18px; flex: none; }
</style>
</head>
<body>
<main class="stage">
  <section class="card card-front" aria-label="Card front">
    <div class="brand"><span class="brand-mark"></span>TMW Home Crafting</div>
  </section>

  <section class="card card-back" aria-label="Card back">
    <div class="brand">
      <span class="brand-mark"></span>
      <span class="brand-name"><span class="brand-line">TMW Home</span><span class="brand-line">Crafting</span></span>
    </div>
    <div class="divider"></div>
    <div class="contact">
      <p class="contact-name">Liam Hartley</p>
      <p class="contact-role">General Manager</p>
      <ul class="contact-list">
        <li>
          <svg class="contact-icon" viewBox="0 0 18 18"><circle cx="9" cy="9" r="9" fill="#1f9a46"/><path d="M6.5 5h2l.7 2-1.2.8a6 6 0 0 0 2.2 2.2l.8-1.2 2 .7v2a1 1 0 0 1-1 1A7 7 0 0 1 5.5 6a1 1 0 0 1 1-1z" fill="#fff"/></svg>
          0400 123 456
        </li>
        <li>
          <svg class="contact-icon" viewBox="0 0 18 18"><circle cx="9" cy="9" r="9" fill="#1f9a46"/><rect x="4.5" y="6" width="9" height="6.5" rx="1" fill="none" stroke="#fff" stroke-width="1.2"/><path d="M4.8 6.4 9 9.6l4.2-3.2" fill="none" stroke="#fff" stroke-width="1.2"/></svg>
          info@tmwhomecrafting.com.au
        </li>
        <li>
          <svg class="contact-icon" viewBox="0 0 18 18"><circle cx="9" cy="9" r="9" fill="#1f9a46"/><circle cx="9" cy="9" r="4.5" fill="none" stroke="#fff" stroke-width="1.1"/><ellipse cx="9" cy="9" rx="2" ry="4.5" fill="none" stroke="#fff" stroke-width="1.1"/><path d="M4.5 9h9" stroke="#fff" stroke-width="1.1"/></svg>
          www.tmwhomecrafting.com.au
        </li>
        <li>
          <svg class="contact-icon" viewBox="0 0 18 18"><circle cx="9" cy="9" r="9" fill="#1f9a46"/><path d="M9 14s-4-4-4-6.8a4 4 0 0 1 8 0C13 10 9 14 9 14z" fill="#fff"/><circle cx="9" cy="7.3" r="1.5" fill="#1f9a46"/></svg>
          Launceston, Tasmania, Australia
        </li>
      </ul>
    </div>
  </section>
</main>
</body>
</html>
```